Pepper & Palm Business Card FUN & EXCITING

Here is the Information for the Card:
Jaswinder Bains (Ravi)
E: RaviBains@postlark.com
C: (480) 555-0147
www.PepperPalmLV.com

We don't want traditional Indian cliche, We a playful bold and fun business card.

Files: https://files.cloudvessel.net/share/folders/7TqRmXpZ2vKa9LwBn4YcHd3JsEf6UoGi?usp=share_link

https://files.cloudvessel.net/share/folders/4MzXaQ8rTw2YbNcVk6PsLe5GhJdR3FoU?usp=share_link

Target Market(s)

Las Vegas Local Restaurant

Industry/Entity Type

Indian Restaurant

Contact Information for Business Card

Name, Email, Cell Phone, Company Logo

```html
<!DOCTYPE html>
<html lang="en">
<head>
<meta charset="utf-8">
<title>Pepper &amp; Palm — Business Card</title>
<link rel="stylesheet" href="https://fonts.googleapis.com/css2?family=Nunito+Sans:wght@400;600;800;900&family=Caveat+Brush&display=swap">
<style>
  :root {
    --backdrop: #8e8e8e;
    --brand-pink: #cc3358;
    --ink: #111111;
    --paper: #ffffff;
    --teal: #00b294;
    --gold: #f2b418;
    --navy: #1e2a55;
    --photo-warm: #b0622a;
    --photo-dark: #3a3f45;
    --sticker-cream: #f3e8d2;
    --sticker-orange: #e98a3c;
  }
  * { box-sizing: border-box; margin: 0; padding: 0; }
  html, body { width: 1200px; height: 1200px; overflow: hidden; }
  body {
    background: var(--backdrop);
    font-family: "Nunito Sans", sans-serif;
    position: relative;
  }
  .card {
    position: absolute;
    top: 246px;
    width: 436px;
    height: 746px;
    overflow: hidden;
  }
  /* Front */
  .card-front { left: 160px; background: var(--brand-pink); color: var(--paper); }
  .front-quote {
    position: absolute; top: 64px; left: 0; right: 0;
    text-align: center; font-size: 18px; line-height: 1.35; font-weight: 400;
  }
  .front-name {
    position: absolute; top: 200px; left: 30px; right: 30px;
    text-align: center; font-weight: 900; font-size: 72px; line-height: 0.95;
    color: var(--ink); text-transform: uppercase; letter-spacing: -1px;
  }
  .front-illustration {
    position: absolute; top: 370px; left: 40px; width: 356px; height: 250px;
    border-radius: 40px;
    background: radial-gradient(ellipse at 50% 45%, var(--sticker-cream) 0%, #e9d6b8 55%, var(--sticker-orange) 120%);
  }
  /* Back */
  .card-back { left: 642px; background: var(--paper); }
  .back-photo {
    position: absolute; top: 0; left: 0; right: 0; height: 166px;
    background: linear-gradient(120deg, var(--photo-dark) 0%, var(--photo-warm) 45%, #d08a3e 70%, #9aa3a8 100%);
  }
  .back-logo-name {
    position: absolute; top: 170px; left: 0; right: 0;
    text-align: center; font-weight: 900; font-size: 44px; color: var(--brand-pink);
    text-transform: uppercase; letter-spacing: -0.5px;
  }
  .person-name {
    position: absolute; top: 300px; left: 0; right: 0; text-align: center;
    font-family: "Caveat Brush", cursive; font-size: 54px; color: var(--brand-pink);
    text-transform: uppercase; letter-spacing: 1px;
  }
  .person-nickname {
    position: absolute; top: 372px; left: 0; right: 0; text-align: center;
    font-family: "Caveat Brush", cursive; font-size: 40px; color: var(--gold);
  }
  .contact-icons {
    position: absolute; top: 438px; left: 0; right: 0;
    display: flex; justify-content: center; gap: 5px;
  }
  .contact-icons svg { width: 32px; height: 32px; }
  .contact-list {
    position: absolute; top: 488px; left: 0; right: 0; text-align: center;
    list-style: none; font-size: 20px; line-height: 27px; color: var(--navy);
  }
  .social-row {
    position: absolute; top: 606px; left: 0; right: 0;
    display: flex; justify-content: center; gap: 14px;
    font-size: 13px; font-weight: 600; color: var(--navy);
  }
  .social-item { display: flex; align-items: center; gap: 5px; }
  .social-item .dot { width: 14px; height: 14px; background: var(--brand-pink); }
  .address-band {
    position: absolute; bottom: 0; left: 0; right: 0; height: 78px;
    background: var(--teal); color: var(--paper);
    display: flex; flex-direction: column; justify-content: center; align-items: center;
    font-size: 19px; line-height: 25px;
  }
</style>
</head>
<body>
  <section class="card card-front">
    <p class="front-quote">“Voted Best Indian Restaurant In America”<br>- Mom &amp; Dad</p>
    <h1 class="front-name">Pepper &amp; Palm</h1>
    <div class="front-illustration" role="img" aria-label="Cartoon sticker of a curry bowl and a naan walking together, with hearts and sparkles"></div>
  </section>

  <section class="card card-back">
    <div class="back-photo" role="img" aria-label="Top-down photo of Indian dishes: tandoori chicken, curries and puffed bread"></div>
    <p class="back-logo-name">Pepper &amp; Palm</p>
    <h2 class="person-name">Jaswinder Bains</h2>
    <p class="person-nickname">( Ravi )</p>

    <div class="contact-icons">
      <svg viewBox="0 0 32 32" aria-label="Phone"><circle cx="16" cy="16" r="16" fill="var(--teal)"/><rect x="11" y="7" width="10" height="18" rx="2" fill="none" stroke="#fff" stroke-width="2"/><circle cx="16" cy="22" r="1" fill="#fff"/></svg>
      <svg viewBox="0 0 32 32" aria-label="Email"><circle cx="16" cy="16" r="16" fill="var(--teal)"/><rect x="8" y="10" width="16" height="12" fill="none" stroke="#fff" stroke-width="2"/><path d="M8 10 L16 17 L24 10" fill="none" stroke="#fff" stroke-width="2"/></svg>
      <svg viewBox="0 0 32 32" aria-label="Website"><circle cx="16" cy="16" r="16" fill="var(--teal)"/><circle cx="16" cy="16" r="8" fill="none" stroke="#fff" stroke-width="1.8"/><ellipse cx="16" cy="16" rx="3.5" ry="8" fill="none" stroke="#fff" stroke-width="1.5"/><path d="M8 16 H24" stroke="#fff" stroke-width="1.5"/></svg>
    </div>

    <ul class="contact-list">
      <li>(480) 555-0147</li>
      <li>ravibains@postlark.com</li>
      <li>pepperpalmlv.com</li>
    </ul>

    <div class="social-row">
      <span class="social-item"><span class="dot"></span>Hubbub</span>
      <span class="social-item"><span class="dot"></span>Pixlo</span>
      <span class="social-item"><span class="dot"></span>Rateful</span>
    </div>

    <address class="address-band" style="font-style:normal">
      <span>2180 W Sunset Ridge Rd. Ste 210</span>
      <span>Las Vegas, NV 89118</span>
    </address>
  </section>
</body>
</html>
```